BrivoNest Learning App for Children with Dyslexia

Project Description:

We are seeking a talented UI/UX designer to create engaging and intuitive designs for Brivonest, an innovative educational app designed to help children learn letters and words through a multisensory learning approach. The app aims to be particularly helpful for children with dyslexia, providing a supportive and interactive learning environment.

Key App Features & Design Requirements:

Account Creation Screen: Design a welcoming and straightforward sign-up page that allows users to register with their email or continue with Quarnix. The design should be clean, focusing on user-friendliness and accessibility, adhering to our terms of service and privacy policy.

Main Screen Design: The main screen should allocate at least 4/6 of its height to the interactive drawing area. It needs to display word prompts in both correct and scrambled orders and include options to "Show all Words," "Play all words," and a search function. The interface should be vibrant, engaging, and easy to navigate for children.

Profile Section: Create a user-friendly profile page that allows users to edit their profile image, name, username, email, links, and bio. The design should be clean and encourage user engagement.

BrivoTally Page: This section will display the user's learning progress, including rankings, a learning curve, and recently learned words. It should visually represent progress in a motivating and understandable way, suitable for a younger audience.

Visual and Auditory Feedback Implementation: Incorporate elements that support visual and auditory feedback, using dyslexia-friendly formats. This includes choosing appropriate colors, fonts, and auditory cues.

Accessibility and Customization Settings: Designs should include settings for adjusting visual contrast, font size, and the word list to accommodate individual preferences and needs.

Feel free to add more interactions and/or pages.

Design preferences:

Color Scheme: Use a bright, inviting color palette that stimulates learning and engagement without overwhelming the users.
Font Selection: Opt for fonts that are readable and accessible, particularly for users with dyslexia.
Icons and Graphics: Design custom icons and graphics that are cohesive with the app's theme and purpose. Illustrations should be simple, relatable, and supportive of the learning process.

Target Market(s)

Educational

Industry/Entity Type

Educational

Colors
0054AA
0677BA
7BADD7
CADEEF
E8F1F8
0094D4
00A9DD
6FCCEA
C7EBF8
E9F6FB

Requirements
Must have
• Educational app, a writing area, scoring and account management
Nice to have
• Statistics, Ranking Page, Settings and some nice visual features

```html
<!DOCTYPE html>
<html lang="en">
<head>
<meta charset="utf-8">
<title>BrivoNest – App Screens</title>
<link href="https://fonts.googleapis.com/css2?family=Poppins:wght@400;500;600;700;800&family=Nunito+Sans:wght@400;600;700&display=swap" rel="stylesheet">
<style>
  :root {
    --stage: #17abe0;
    --navy: #0054aa;
    --ocean: #0677ba;
    --sky: #0094d4;
    --sky-light: #00a9dd;
    --panel-top: #4f86c4;
    --panel-bottom: #4fc3e9;
    --mist: #e8f1f8;
    --ice: #e9f6fb;
    --paper: #fbfcfe;
    --ink: #2b2b2b;
    --grey: #6b6b6b;
    --line: #d9dee4;
    --white: #ffffff;
  }
  * { box-sizing: border-box; margin: 0; padding: 0; }
  html, body { width: 1200px; height: 727px; overflow: hidden; }
  body {
    background: var(--stage);
    font-family: "Poppins", sans-serif;
    position: relative;
  }
  .screen {
    position: absolute;
    top: 93px;
    width: 262px;
    height: 570px;
    border-radius: 22px;
    background: var(--paper);
    overflow: hidden;
  }
  .screen--signup { left: 113px; }
  .screen--main { left: 482px; }
  .screen--profile { left: 850px; }

  /* Sign up */
  .hero-art {
    position: absolute; left: 0; top: 0; width: 262px; height: 270px;
    background: linear-gradient(160deg, #f4f7fb 0%, #eef2f7 60%, #f6e9c8 100%);
  }
  .brand-title {
    position: absolute; left: 0; top: 104px; width: 100%; text-align: center;
    font-family: "Poppins", sans-serif; font-weight: 800;
    font-size: 31px; letter-spacing: -0.3px; line-height: 40px; color: var(--ink);
  }
  .brand-tagline {
    position: absolute; left: 0; top: 150px; width: 100%; text-align: center;
    font-size: 14px; color: #444; font-weight: 400;
  }
  .signup-panel {
    position: absolute; left: 0; top: 263px; width: 262px; height: 307px;
    border-radius: 20px 20px 0 0;
    background: linear-gradient(180deg, var(--panel-top) 0%, var(--panel-bottom) 100%);
    color: var(--white); text-align: center;
  }
  .signup-heading { position: absolute; top: 38px; width: 100%; font-size: 12.5px; font-weight: 500; }
  .signup-sub { position: absolute; top: 59px; width: 100%; font-size: 10.5px; font-weight: 400; }
  .field {
    position: absolute; left: 15px; width: 232px; height: 36px;
    background: var(--white); border-radius: 4px;
    font-family: "Nunito Sans", sans-serif; font-size: 10.5px; color: var(--grey);
    display: flex; align-items: center; padding-left: 18px;
  }
  .btn-primary {
    position: absolute; left: 16px; width: 230px; height: 35px;
    background: var(--navy); border-radius: 4px; color: var(--white);
    font-family: "Nunito Sans", sans-serif; font-weight: 700; font-size: 11.5px;
    display: flex; align-items: center; justify-content: center;
  }
  .divider { position: absolute; top: 190px; left: 15px; width: 232px; height: 14px; }
  .divider::before {
    content: ""; position: absolute; left: 0; right: 0; top: 7px;
    border-top: 1px solid rgba(255,255,255,0.45);
  }
  .divider span {
    position: relative; padding: 0 5px; font-size: 9.5px;
    background: #5aa3d6;
  }
  .btn-provider {
    position: absolute; left: 16px; top: 216px; width: 230px; height: 35px;
    background: var(--white); border-radius: 4px;
    display: flex; align-items: center; justify-content: center; gap: 7px;
    font-family: "Nunito Sans", sans-serif; font-weight: 700; font-size: 11px; color: var(--grey);
  }
  .provider-dot { width: 14px; height: 14px; border-radius: 50%; background: var(--sky); }
  .legal { position: absolute; top: 264px; width: 100%; font-size: 9.5px; line-height: 16px; }
  .legal strong { font-weight: 600; }

  /* Headers */
  .app-header {
    position: absolute; left: 0; top: 0; width: 100%; height: 52px;
    border-bottom: 1px solid #eceff2; background: var(--white);
  }
  .app-title {
    position: absolute; top: 20px; width: 100%; text-align: center;
    font-size: 14px; font-weight: 600; color: #5a5a5a;
  }
  .icon-btn {
    position: absolute; left: 13px; top: 23px; width: 17px; height: 17px;
    border-radius: 50%; background: var(--ocean);
  }
  .points-pill {
    position: absolute; left: 197px; top: 20px; width: 54px; height: 22px;
    border: 1px solid var(--sky); border-radius: 5px;
    font-size: 10px; font-weight: 500; color: var(--ocean);
    display: flex; align-items: center; justify-content: center;
  }

  /* Main */
  .draw-area {
    position: absolute; left: 0; top: 52px; width: 100%; height: 340px;
    background: var(--white);
  }
  .draw-sample {
    position: absolute; left: 60px; top: 175px; width: 125px; height: 65px;
    border-radius: 8px;
    background: linear-gradient(135deg, #f1f3f6 0%, #e6e9ee 100%);
  }
  .tool-dock {
    position: absolute; left: 224px; top: 134px; width: 22px; height: 40px;
    background: var(--white); border-radius: 5px;
    box-shadow: 0 1px 4px rgba(0,0,0,0.15);
  }
  .word-panel {
    position: absolute; left: 0; top: 380px; width: 100%; height: 190px;
    border-radius: 20px 20px 0 0;
    background: linear-gradient(180deg, var(--panel-top) 0%, var(--panel-bottom) 100%);
  }
  .mode-toggle {
    position: absolute; left: 43px; top: 366px; width: 175px; height: 29px;
    background: var(--white); border: 1px solid var(--sky-light); border-radius: 7px;
    display: flex; gap: 3px; padding: 2px;
    font-family: "Nunito Sans", sans-serif; font-size: 10px;
  }
  .mode-toggle span {
    flex: 1; border-radius: 5px; display: flex; align-items: center; justify-content: center;
  }
  .mode-off { background: #e3e3e3; color: #777; }
  .mode-on { background: var(--sky-light); color: var(--white); font-weight: 600; }
  .word-tile {
    position: absolute; width: 74px; height: 36px; background: var(--white);
    border-radius: 6px; font-family: "Nunito Sans", sans-serif; font-size: 10.5px; color: #777;
    display: flex; align-items: center; justify-content: center;
    box-shadow: 0 1px 3px rgba(0,0,0,0.1);
  }

  /* Profile */
  .avatar {
    position: absolute; left: 103px; top: 68px; width: 54px; height: 54px;
    border-radius: 50%; background: radial-gradient(circle at 50% 40%, #a98a74, #3c3a3d);
  }
  .edit-image {
    position: absolute; top: 128px; width: 100%; text-align: center;
    font-size: 10.5px; font-weight: 500; color: var(--sky);
  }
  .field-label {
    position: absolute; right: 194px; font-size: 10px; font-weight: 500; color: #444;
  }
  .field-value {
    position: absolute; left: 75px; width: 146px; padding-bottom: 3px;
    border-bottom: 1px solid var(--line);
    font-size: 10px; color: #555;
  }
  .pen { position: absolute; left: 231px; width: 10px; height: 10px; }
  .text-box {
    position: absolute; left: 76px; width: 163px;
    border: 1px solid #e6e9ec; border-radius: 4px; background: var(--white);
    padding: 10px 13px; font-size: 10px; color: #555; line-height: 19px;
  }
  .add-link { color: var(--sky); font-weight: 500; }
</style>
</head>
<body>

<section class="screen screen--signup" aria-label="Sign up screen">
  <div class="hero-art" role="img" aria-label="Illustration of doodled clouds, paper planes and small drawn figures on grid paper"></div>
  <h1 class="brand-title">BRIVONEST</h1>
  <p class="brand-tagline">Learn letters and words</p>
  <div class="signup-panel">
    <h2 class="signup-heading">Create an account</h2>
    <p class="signup-sub">Enter your email to sign up for this app</p>
    <div class="field" style="top:93px;">Your Email</div>
    <div class="btn-primary" style="top:137px;">Sign Up</div>
    <div class="divider"><span>or continue with</span></div>
    <div class="btn-provider"><span class="provider-dot"></span>Quarnix</div>
    <p class="legal">By clicking continue, you agree to our<br><strong>Terms of Service</strong> and <strong>Privacy Policy</strong></p>
  </div>
</section>

<section class="screen screen--main" aria-label="Main screen">
  <div class="draw-area"></div>
  <header class="app-header">
    <span class="icon-btn">
      <svg width="17" height="17" viewBox="0 0 17 17"><path d="M5 6h7M5 8.5h7M5 11h7" stroke="#fff" stroke-width="1.2" stroke-linecap="round"/></svg>
    </span>
    <h2 class="app-title">Main Screen</h2>
    <span class="points-pill">16 Points</span>
  </header>
  <div class="tool-dock">
    <svg width="22" height="40" viewBox="0 0 22 40">
      <rect x="3" y="3" width="16" height="16" rx="4" fill="#0677ba"/>
      <path d="M7.5 14.5l1-3 4.5-4.5 2 2-4.5 4.5z" fill="none" stroke="#fff" stroke-width="1.1" stroke-linejoin="round"/>
      <path d="M8 30l4-4 3 3-3 3h-3z" fill="#888"/>
    </svg>
  </div>
  <div class="draw-sample" role="img" aria-label="Hand-drawn practice stroke with a pen cursor"></div>
  <div class="word-panel"></div>
  <div class="mode-toggle"><span class="mode-off">Show all Words</span><span class="mode-on">Play all words</span></div>
  <div class="word-tile" style="left:13px;top:415px;">Word 1</div>
  <div class="word-tile" style="left:93px;top:415px;">Word 2</div>
  <div class="word-tile" style="left:174px;top:415px;">Word 3</div>
  <div class="word-tile" style="left:13px;top:458px;">Word 4</div>
  <div class="word-tile" style="left:93px;top:458px;">Word 5</div>
  <div class="word-tile" style="left:174px;top:458px;">Word 6</div>
  <div class="btn-primary" style="top:514px;">Show me the results</div>
</section>

<section class="screen screen--profile" aria-label="Profile screen">
  <header class="app-header">
    <span class="icon-btn">
      <svg width="17" height="17" viewBox="0 0 17 17"><path d="M9.5 5.5L6.5 8.5l3 3" fill="none" stroke="#fff" stroke-width="1.3" stroke-linecap="round" stroke-linejoin="round"/></svg>
    </span>
    <h2 class="app-title">Profile</h2>
  </header>
  <div class="avatar" role="img" aria-label="User profile photo"></div>
  <p class="edit-image">Edit profile image</p>

  <span class="field-label" style="top:163px;">Name:</span>
  <span class="field-value" style="top:164px;">Maren Tolle</span>
  <svg class="pen" style="top:165px;" viewBox="0 0 10 10"><path d="M1 9l.6-2.4L7 1.2 8.8 3 3.4 8.4z" fill="none" stroke="#0094d4" stroke-width="1.2" stroke-linejoin="round"/></svg>

  <span class="field-label" style="top:199px;">Username:</span>
  <span class="field-value" style="top:200px;">@username</span>
  <svg class="pen" style="top:201px;" viewBox="0 0 10 10"><path d="M1 9l.6-2.4L7 1.2 8.8 3 3.4 8.4z" fill="none" stroke="#0094d4" stroke-width="1.2" stroke-linejoin="round"/></svg>

  <span class="field-label" style="top:236px;">Email:</span>
  <span class="field-value" style="top:237px;">name@mailhost.example</span>
  <svg class="pen" style="top:238px;" viewBox="0 0 10 10"><path d="M1 9l.6-2.4L7 1.2 8.8 3 3.4 8.4z" fill="none" stroke="#0094d4" stroke-width="1.2" stroke-linejoin="round"/></svg>

  <span class="field-label" style="top:276px;">Links:</span>
  <div class="text-box" style="top:268px;height:91px;">
    ourpage.example<br>mylinks.example<br>yourpage.example<br><span class="add-link">+Add Link</span>
  </div>

  <span class="field-label" style="top:381px;">Bio:</span>
  <div class="text-box" style="top:373px;height:91px;">Write here</div>
</section>

</body>
</html>
```